New & Improved KIVORA Business Card

I would like a two sided business card one side dedicated to home automation (security camera installation, television & sound bar mounting (hidden wires optional) , sink installation, fireplace mounting, chandelier installation and one side dedicated to all electronic repairs, In ex: plume band repairs, computer, zTab, laptop repairs, Velofon's, Korvex and etc.. Using the colors on this flyer. The phone number &email I want on both sides is (555) 214-3907 & Tech@Kivora.help. SAME COLOR AS THE FLYER ATTACHED.

Target Market(s)

EVERYONE.

Contact Information for Business Card

I would like a two sided business card one side dedicated to home automation (security camera installation, television & sound bar mounting (hidden wires optional) , sink installation, fireplace mounting, chandelier installation and one side dedicated to all electronic repairs, In ex: plume band repairs, computer, zTab, laptop repairs, Velofon's, Korvex and etc.. Using the colors on this flyer. The phone number &email I want on both sides is (555) 214-3907 & Tech@Kivora.help

Requirements
Must have
• -TV MOUNTING
-HOME AUTOMATION
-SECURITY CAMERA INSTALLATION
-ALL ELECTRONIC REPAIRS
- (555) 214-3907
-Tech@Kivora.help
-SAME COLOR AS THE FLYER
Nice to have
• Same colors & concept as the flyer attached below.
Should not have
• DO NOT DO A DIFF COLOR I WANT SAME COLOR AS THE FLYER ATTACHED.

```html
<!DOCTYPE html>
<html lang="en">
<head>
<meta charset="utf-8">
<title>KIVORA Business Card</title>
<link rel="stylesheet" href="https://fonts.googleapis.com/css2?family=Montserrat:wght@400;500&family=Open+Sans:wght@400;600;700;800&display=swap">
<style>
  :root {
    --pink: #e8439a;
    --pink-light: #f06db3;
    --pink-deep: #d62f88;
    --ink: #1b1b1d;
    --charcoal: #2b2b2e;
    --charcoal-light: #48484c;
    --paper: #ffffff;
    --mist: #eeeeef;
    --grey: #c9c9cc;
    --stage: #e4e4e6;
  }
  * { box-sizing: border-box; margin: 0; padding: 0; }
  html, body { width: 1200px; height: 780px; overflow: hidden; }
  body {
    background: var(--stage);
    font-family: "Open Sans", Arial, sans-serif;
    position: relative;
  }
  .card {
    position: absolute;
    top: 57px;
    width: 380px;
    height: 665px;
    overflow: hidden;
    box-shadow: 0 10px 30px rgba(0,0,0,.18);
  }
  .wordmark {
    font-family: "Montserrat", Arial, sans-serif;
    font-weight: 400;
    letter-spacing: 12px;
    position: absolute;
    left: 0; right: 0;
    text-align: center;
  }

  /* Repairs side */
  .card--repairs { left: 175px; background: var(--paper); }
  .repairs__hero {
    position: absolute; inset: 0 0 auto 0; height: 300px;
    background: linear-gradient(160deg, var(--pink-light) 0%, var(--pink) 45%, var(--pink-deep) 100%);
  }
  .repairs__hero .wordmark { top: 92px; font-size: 28px; color: var(--paper); }
  .device-frame {
    position: absolute; border: 1px solid rgba(255,255,255,.25);
    border-radius: 4px;
  }
  .device-label {
    position: absolute; font-size: 9px; font-weight: 700; letter-spacing: 1px;
    color: rgba(255,255,255,.45); text-transform: uppercase;
  }
  .repairs__facets { position: absolute; left: 0; top: 230px; width: 380px; height: 200px; }
  .repairs__art {
    position: absolute; left: 70px; top: 248px; width: 240px; height: 150px;
    background: linear-gradient(180deg, #e9e9eb 0%, #bdbdc1 60%, #2a2a2d 100%);
    border-radius: 6px;
  }
  .repairs__pitch {
    position: absolute; top: 425px; left: 0; right: 0; text-align: center;
    font-size: 17px; font-weight: 600; line-height: 1.2; color: var(--ink);
    text-transform: uppercase;
  }
  .repairs__headline {
    position: absolute; top: 478px; left: 0; right: 0; text-align: center;
    font-size: 21px; font-weight: 800; color: var(--pink); text-transform: uppercase;
  }
  .contact-pill {
    position: absolute; top: 516px; left: 20px; right: 20px; height: 40px;
    border-radius: 20px; background: linear-gradient(180deg, #3a3a3d, var(--ink));
    display: flex; align-items: center; justify-content: center; gap: 8px;
    color: var(--pink); font-size: 20px; font-weight: 700;
  }
  .contact-pill--email {
    top: 566px; left: 20px; right: 20px; height: 34px; border-radius: 17px;
    background: linear-gradient(180deg, #f5f5f6, #dcdcde);
    justify-content: flex-start; padding-left: 36px;
    color: var(--ink); font-size: 17px; font-weight: 400;
  }

  /* Home automation side */
  .card--automation {
    left: 645px;
    background: linear-gradient(165deg, var(--charcoal-light) 0%, var(--charcoal) 35%, var(--ink) 100%);
  }
  .card--automation .wordmark { top: 48px; font-size: 36px; color: var(--pink); }
  .automation__title {
    position: absolute; top: 100px; left: 0; right: 0; text-align: center;
    font-size: 19px; font-weight: 700; color: var(--paper); text-transform: uppercase;
  }
  .service-list {
    position: absolute; top: 160px; left: 48px; right: 30px; list-style: none;
  }
  .service-list li {
    display: flex; gap: 12px; color: var(--paper);
    font-size: 16px; line-height: 1.2; margin-bottom: 18px;
  }
  .service-list svg { flex: none; margin-top: 2px; }
  .feature-pill {
    position: absolute; top: 405px; left: 30px; right: 30px; height: 38px;
    border-radius: 19px; background: var(--pink);
    color: var(--paper); font-size: 17px; font-weight: 800;
    display: flex; align-items: center; justify-content: center; text-transform: uppercase;
  }
  .automation__chevron { position: absolute; left: 0; bottom: 0; width: 380px; height: 300px; }
  .automation__phone {
    position: absolute; left: 30px; bottom: 40px;
    display: flex; align-items: center; gap: 8px;
    color: var(--paper); font-size: 20px; font-weight: 700;
  }
</style>
</head>
<body>

<section class="card card--repairs" aria-label="Electronic repairs side">
  <div class="repairs__hero">
    <div class="device-frame" style="left:28px;top:70px;width:90px;height:70px"></div>
    <span class="device-label" style="left:40px;top:152px">Laptops</span>
    <div class="device-frame" style="left:160px;top:60px;width:60px;height:90px"></div>
    <span class="device-label" style="left:168px;top:162px">Mobiles</span>
    <div class="device-frame" style="left:262px;top:70px;width:80px;height:90px"></div>
    <span class="device-label" style="left:280px;top:172px">Tablets</span>
    <div class="wordmark">KIVORA</div>
  </div>
  <svg class="repairs__facets" viewBox="0 0 380 200" aria-hidden="true">
    <polygon points="0,70 190,20 380,70 380,200 0,200" fill="#ffffff"/>
    <polygon points="0,70 120,40 80,140 0,170" fill="#e3e3e5"/>
    <polygon points="380,70 260,40 300,140 380,170" fill="#e3e3e5"/>
  </svg>
  <div class="repairs__art" role="img" aria-label="Illustration of a monitor, tablets, phone and smartwatch with cracked screens"></div>
  <p class="repairs__pitch">For any repairs, we come to you,<br>with unbeatable prices</p>
  <p class="repairs__headline">All Electronic Repairs</p>
  <div class="contact-pill">
    <svg width="18" height="22" viewBox="0 0 18 22" aria-hidden="true"><rect x="3" y="1" width="12" height="20" rx="2" fill="none" stroke="currentColor" stroke-width="2"/><circle cx="9" cy="17" r="1.3" fill="currentColor"/></svg>
    <span>(555) 214-3907</span>
  </div>
  <div class="contact-pill contact-pill--email">
    <svg width="18" height="14" viewBox="0 0 18 14" aria-hidden="true" style="margin-right:4px"><rect x="1" y="1" width="16" height="12" rx="1" fill="none" stroke="#1b1b1d" stroke-width="1.5"/><polyline points="1,1 9,8 17,1" fill="none" stroke="#1b1b1d" stroke-width="1.5"/></svg>
    <span>Tech@Kivora.help</span>
  </div>
</section>

<section class="card card--automation" aria-label="Home automation side">
  <div class="wordmark">KIVORA</div>
  <p class="automation__title">Home Automation</p>
  <ul class="service-list">
    <li><svg width="16" height="16" viewBox="0 0 16 16" aria-hidden="true"><circle cx="8" cy="8" r="8" fill="#e8439a"/><polyline points="6,4.5 10,8 6,11.5" fill="none" stroke="#fff" stroke-width="2"/></svg>Security Camera Installation</li>
    <li><svg width="16" height="16" viewBox="0 0 16 16" aria-hidden="true"><circle cx="8" cy="8" r="8" fill="#e8439a"/><polyline points="6,4.5 10,8 6,11.5" fill="none" stroke="#fff" stroke-width="2"/></svg>Sink Installation</li>
    <li><svg width="16" height="16" viewBox="0 0 16 16" aria-hidden="true"><circle cx="8" cy="8" r="8" fill="#e8439a"/><polyline points="6,4.5 10,8 6,11.5" fill="none" stroke="#fff" stroke-width="2"/></svg>Fireplace Mounting</li>
    <li><svg width="16" height="16" viewBox="0 0 16 16" aria-hidden="true"><circle cx="8" cy="8" r="8" fill="#e8439a"/><polyline points="6,4.5 10,8 6,11.5" fill="none" stroke="#fff" stroke-width="2"/></svg>Chandelier Installation</li>
    <li><svg width="16" height="16" viewBox="0 0 16 16" aria-hidden="true"><circle cx="8" cy="8" r="8" fill="#e8439a"/><polyline points="6,4.5 10,8 6,11.5" fill="none" stroke="#fff" stroke-width="2"/></svg><span>Television &amp; Sound Bar Mounting<br>(Hidden Wires Optional)</span></li>
  </ul>
  <div class="feature-pill">Professional TV Mounting</div>
  <svg class="automation__chevron" viewBox="0 0 380 300" aria-hidden="true">
    <polygon points="300,0 380,0 380,60" fill="#e8439a"/>
    <polygon points="0,95 150,170 380,40 380,72 150,205 0,128" fill="#ffffff"/>
    <polygon points="0,128 150,205 380,72 380,300 0,300" fill="#e8439a"/>
  </svg>
  <div class="automation__phone">
    <svg width="18" height="22" viewBox="0 0 18 22" aria-hidden="true"><rect x="3" y="1" width="12" height="20" rx="2" fill="none" stroke="#fff" stroke-width="2"/><circle cx="9" cy="17" r="1.3" fill="#fff"/></svg>
    <span>(555) 214-3907</span>
  </div>
</section>

</body>
</html>
```